Calden L - Premium Business Cards

Background of Calden L
Calden Leafworks is a cigar mobile lounge where guests become family. A place of luxury, relaxation, and ambiance is the global popularity demand. Calden Leafworks strives to provide first-class service of quality and products. Our goal is to ensure that every guest is treated and serviced as a VIP.

Calden Leafworks was founded by Dennis Markow Jr in January 2020. After 15 years of cigar reviews and research Dennis decided it was time to launch his own cigar brand and boutique cigar company. With a wealth of knowledge and years of experience Calden Leafworks was born. With opulence for all cultures, Calden Leafworks offers hand rolled cigars with premium blend tobacco from sweet to bold imported from Costa Rica, Dominican Republic, and Nicaragua. Thank you for your business!

Objective:
Create a business card template to be used for all employees. Design should communicate premium and classy. And should use earth tone colors.

Design should include:
1. Client wants to incorporate the cigar leaf
2. Logo
3. Tagline: Respect the smoke
3. Content info:
Kevin Oldacre
Owner
555-017-4863
koldacre@caldenleaf.com
caldenleafworks.com

```html
<!DOCTYPE html>
<html lang="en">
<head>
<meta charset="utf-8">
<title>Calden Leafworks – Business Cards</title>
<link href="https://fonts.googleapis.com/css2?family=Open+Sans:wght@400;700&display=swap" rel="stylesheet">
<style>
  :root{
    --stage:#e6e6e4;
    --ink:#1b1b1b;
    --card-dark:#111111;
    --card-light:#ffffff;
    --muted:#8a8a8a;
    --rule:#3a3a3a;
    --shine-a:#2c2c2c;
    --shine-b:#6d6d6d;
  }
  *{margin:0;padding:0;box-sizing:border-box}
  html,body{width:1200px;height:913px;overflow:hidden}
  body{background:var(--stage);font-family:"Open Sans",sans-serif;position:relative}

  .card{position:absolute;width:520px;height:300px;border-radius:18px;overflow:hidden;box-shadow:0 14px 30px rgba(0,0,0,.22)}

  /* front */
  .card-front{left:100px;top:110px;background:var(--card-dark)}
  .front-art{position:absolute;left:0;top:0;width:100%;height:110px;
    background:linear-gradient(160deg,var(--card-dark) 25%,var(--shine-a) 60%,var(--shine-b) 100%)}
  .front-art-side{position:absolute;right:0;top:0;width:60px;height:200px;
    background:linear-gradient(180deg,var(--shine-b),var(--shine-a))}
  .front-logo{position:absolute;left:0;right:0;top:168px;text-align:center;
    color:var(--card-light);font-weight:700;font-size:40px;letter-spacing:2px;line-height:1.1}

  /* back */
  .card-back{left:580px;top:500px;background:var(--card-light);color:var(--ink)}
  .back-logo{position:absolute;left:28px;width:210px;top:118px;text-align:center;
    font-weight:700;font-size:29px;letter-spacing:1px;line-height:1.15;color:var(--ink)}
  .divider{position:absolute;left:252px;top:52px;width:1px;height:130px;background:var(--rule)}
  .contact{position:absolute;left:272px;top:52px}
  .contact-name{font-weight:700;font-size:19px;letter-spacing:.5px;text-transform:uppercase}
  .contact-role{font-size:13px;color:var(--muted);margin:2px 0 14px}
  .contact-list{list-style:none;font-size:14px;color:#4a4a4a}
  .contact-list li{display:flex;align-items:center;gap:8px;margin-bottom:5px}
  .contact-list svg{width:12px;height:12px;fill:var(--ink);flex:none}
  .tagline{position:absolute;left:272px;top:232px;font-size:14px;text-transform:uppercase;letter-spacing:.5px}
</style>
</head>
<body>
  <section class="card card-front">
    <div class="front-art" role="img" aria-label="Flowing cigar leaf illustration in glossy grey"></div>
    <div class="front-art-side" role="img" aria-label="Cigar wrapper illustration along the edge"></div>
    <div class="front-logo">CALDEN LEAFWORKS</div>
  </section>

  <section class="card card-back">
    <div class="back-logo">CALDEN LEAFWORKS</div>
    <div class="divider"></div>
    <div class="contact">
      <p class="contact-name">Kevin Oldacre</p>
      <p class="contact-role">Owner</p>
      <ul class="contact-list">
        <li><svg viewBox="0 0 24 24"><path d="M6.6 10.8a15 15 0 0 0 6.6 6.6l2.2-2.2a1 1 0 0 1 1-.25 11.4 11.4 0 0 0 3.6.57 1 1 0 0 1 1 1V20a1 1 0 0 1-1 1A17 17 0 0 1 3 4a1 1 0 0 1 1-1h3.5a1 1 0 0 1 1 1c0 1.25.2 2.45.57 3.6a1 1 0 0 1-.25 1z"/></svg>555-017-4863</li>
        <li><svg viewBox="0 0 24 24"><path d="M2 5h20v14H2zm2 2v.5l8 5 8-5V7z"/></svg>koldacre@caldenleaf.com</li>
        <li><svg viewBox="0 0 24 24"><circle cx="12" cy="12" r="10"/></svg>caldenleafworks.com</li>
      </ul>
    </div>
    <p class="tagline">Respect the smoke</p>
  </section>
</body>
</html>
```